Upmarket Dessert Lounge needs a Business Card Design

We are an upmarket dessert lounge needing a business card to match our image.

We want something that is simple yet beautiful, feminine, classy, sophisticated and elegant. We want it to stand out and don't mind if it is bold.

The design should include our logo and colours of red or maroon with gold highlights. We don't mind if black is used.

Marlow & Quince

Target Market(s)

For those who like to indulge or treat themselves and give in to their temptations on good quality desserts.

Industry/Entity Type

Business

Requirements
Must have
• Must include our logo and our name

Marlow & Quince

M & Q

```html
<!DOCTYPE html>
<html lang="en">
<head>
<meta charset="utf-8">
<title>Marlow &amp; Quince – Business Card</title>
<link href="https://fonts.googleapis.com/css2?family=Open+Sans:wght@400;600;700&display=swap" rel="stylesheet">
<style>
  :root {
    --maroon: #7b1518;
    --maroon-deep: #6e1114;
    --peach: #fdd09a;
    --cream: #f9d9a4;
    --ink: #2b2b2b;
    --ink-soft: #3a3a3a;
    --paper: #ffffff;
    --backdrop: #e9e9ea;
  }
  * { margin: 0; padding: 0; box-sizing: border-box; }
  html, body {
    width: 956px; height: 1200px; overflow: hidden;
    background: var(--backdrop);
    font-family: "Open Sans", Arial, sans-serif;
  }
  .canvas { position: relative; width: 956px; height: 1200px; }

  .card {
    position: absolute;
    width: 798px; height: 455px;
    border-radius: 28px;
    overflow: hidden;
  }
  .card--front { left: 79px; top: 85px; background: var(--paper); }
  .card--back  { left: 73px; top: 632px; background: var(--maroon); }

  .brand-name {
    position: absolute; left: 0; right: 0; top: 120px;
    text-align: center;
    font-size: 40px; font-weight: 600; letter-spacing: 2px;
    color: var(--maroon);
  }

  .contact-band { position: absolute; left: 0; top: 290px; width: 798px; height: 97px; }

  .person {
    position: absolute; left: 61px; top: 315px;
    color: var(--paper); text-align: left;
  }
  .person__name { font-size: 20px; font-weight: 700; line-height: 26px; }
  .person__role { font-size: 20px; font-weight: 400; line-height: 26px; }

  .details {
    position: absolute; right: 24px; top: 296px;
    text-align: right; color: var(--ink);
    font-size: 17.5px; line-height: 29px;
  }
  .details b { font-weight: 700; }

  .phones {
    position: absolute; left: 0; right: 0; top: 407px;
    text-align: center; font-size: 20px; color: var(--ink-soft);
    word-spacing: 1px;
  }
  .phones b { font-weight: 700; }
  .phones .sep { margin: 0 8px; }

  .monogram {
    position: absolute; left: 0; right: 0; top: 170px;
    text-align: center;
    font-size: 96px; font-weight: 600; letter-spacing: 4px;
    color: var(--cream);
  }
</style>
</head>
<body>
<div class="canvas">

  <section class="card card--front">
    <div class="brand-name">MARLOW &amp; QUINCE</div>

    <svg class="contact-band" viewBox="0 0 798 97" aria-hidden="true">
      <polygon points="0,0 363,0 273,97 0,97" fill="var(--maroon)"/>
      <polygon points="379,0 798,0 798,97 289,97" fill="var(--peach)"/>
    </svg>

    <div class="person">
      <div class="person__name">Your Name</div>
      <div class="person__role">Designation</div>
    </div>

    <div class="details">
      <div><b>e</b> : name@yourwebsite.com</div>
      <div><b>w</b> : www.marlow&amp;quince.com</div>
      <div>0000, Street Name, City Name, Country Code.</div>
    </div>

    <div class="phones">
      <b>p</b> : 123-456-7890<span class="sep">|</span><b>c</b> : 123-456-7890<span class="sep">|</span><b>f</b> : 123-456-7890
    </div>
  </section>

  <section class="card card--back">
    <div class="monogram">M &amp; Q</div>
  </section>

</div>
</body>
</html>
```